Modern Business Card

Modern professional business card with more than just logo and demographic info. Something memorable.

We are a trendy/modern chiropractic group with an emphasis on neurology, hence the minimalist-type brain logo. We want to convey that modern and technical aspect with professionalism and the elite nature of our practice environment.

```html
<!DOCTYPE html>
<html lang="en">
<head>
<meta charset="utf-8">
<title>Keystone Chiropractic – Business Card</title>
<link href="https://fonts.googleapis.com/css2?family=Bitter:wght@400;600;700&display=swap" rel="stylesheet">
<style>
  :root {
    --backdrop: #7b7b7b;
    --brand-blue: #4a80c2;
    --paper-white: #ffffff;
    --card-black: #050607;
    --rule-light: rgba(255,255,255,0.55);
  }
  * { margin: 0; padding: 0; box-sizing: border-box; }
  html, body { width: 1200px; height: 1200px; overflow: hidden; }
  body {
    background: var(--backdrop);
    font-family: "Bitter", Georgia, serif;
    position: relative;
  }
  .card {
    position: absolute;
    top: 310px;
    height: 595px;
    box-shadow: 3px 4px 8px rgba(0,0,0,0.35);
    overflow: hidden;
  }
  /* Front */
  .card-front {
    left: 234px;
    width: 364px;
    background: var(--brand-blue);
    color: var(--paper-white);
    text-align: center;
  }
  .front-top {
    height: 175px;
    background: var(--paper-white);
    display: flex;
    align-items: center;
    justify-content: center;
    gap: 14px;
  }
  .brand-dot {
    width: 34px; height: 34px;
    border-radius: 50%;
    background: var(--brand-blue);
  }
  .brand-name {
    color: var(--brand-blue);
    font-weight: 700;
    font-size: 34px;
    letter-spacing: 2px;
  }
  .holder {
    position: absolute;
    top: 334px; left: 0; right: 0;
  }
  .holder-name {
    font-weight: 700;
    font-size: 24px;
    letter-spacing: 0.3px;
    text-transform: uppercase;
    line-height: 28px;
  }
  .holder-role {
    font-size: 16px;
    line-height: 22px;
  }
  .icon-row {
    position: absolute;
    top: 396px; left: 87px; right: 87px;
    display: flex;
    align-items: center;
    gap: 6px;
  }
  .icon-row .rule { flex: 1; height: 1px; background: var(--rule-light); }
  .icon-row .icon { width: 24px; height: 24px; display: block; }
  .icon-row .rule:first-child { margin-right: 8px; }
  .icon-row .rule:last-child { margin-left: 8px; }
  .contact {
    position: absolute;
    top: 431px; left: 0; right: 0;
    font-size: 16px;
    line-height: 22px;
  }
  .contact-divider {
    position: absolute;
    top: 506px; left: 86px; right: 86px;
    height: 1px;
    background: var(--rule-light);
  }
  .address {
    position: absolute;
    top: 518px; left: 0; right: 0;
    font-size: 16px;
    line-height: 22px;
  }
  /* Back */
  .card-back {
    left: 627px;
    width: 369px;
    background: var(--card-black);
  }
  .back-wordmark {
    position: absolute;
    left: 184px; top: 228px;
    transform: translate(-50%, -50%) rotate(-90deg);
    color: var(--paper-white);
    font-weight: 400;
    font-size: 44px;
    line-height: 48px;
    white-space: nowrap;
    text-transform: uppercase;
    letter-spacing: 1px;
    text-align: left;
  }
  .back-dot {
    position: absolute;
    left: 134px; top: 393px;
    width: 100px; height: 100px;
    border-radius: 50%;
    background: var(--brand-blue);
  }
</style>
</head>
<body>
  <section class="card card-front">
    <div class="front-top">
      <span class="brand-dot"></span>
      <span class="brand-name">KEYSTONE</span>
    </div>
    <div class="holder">
      <p class="holder-name">Daniel Hart</p>
      <p class="holder-role">Managing Director</p>
    </div>
    <div class="icon-row">
      <span class="rule"></span>
      <svg class="icon" viewBox="0 0 24 24" aria-label="Phone">
        <rect width="24" height="24" rx="3" fill="#fff"/>
        <path d="M7 9 Q12 5 17 9 L15.5 11 L14 10 L10 10 L8.5 11 Z M8 12 H16 L17 17 H7 Z" fill="#4a80c2"/>
      </svg>
      <svg class="icon" viewBox="0 0 24 24" aria-label="Email">
        <rect width="24" height="24" rx="3" fill="#fff"/>
        <rect x="6" y="8" width="12" height="8" fill="none" stroke="#4a80c2" stroke-width="1.5"/>
        <path d="M6 8 L12 13 L18 8" fill="none" stroke="#4a80c2" stroke-width="1.5"/>
      </svg>
      <svg class="icon" viewBox="0 0 24 24" aria-label="Website">
        <rect width="24" height="24" rx="3" fill="#fff"/>
        <circle cx="12" cy="12" r="6.5" fill="#4a80c2"/>
        <path d="M12 5.5 V18.5 M5.5 12 H18.5" stroke="#fff" stroke-width="1"/>
      </svg>
      <span class="rule"></span>
    </div>
    <div class="contact">
      <p>044-555 018 247</p>
      <p>info@keystonechiro.example</p>
      <p>www.keystonechiro.example</p>
    </div>
    <div class="contact-divider"></div>
    <div class="address">
      <p>421, Address line here,</p>
      <p>45452,Country Name</p>
    </div>
  </section>

  <section class="card card-back">
    <p class="back-wordmark">Keystone<br>Chiropractic</p>
    <span class="back-dot"></span>
  </section>
</body>
</html>
```